2 x Digitize Logo | 2 x Business Cards | 2 x Fridge Magnets

We require 6 deliverables:
1. Residential logo redrawn (same just high quality for large print format).
2. Corporate logo redrawn (minor changes to wording and high quality for large print format).
3. New business card design for Furniture Removals (residential)
4. New business card design for Corporate Relocations (business)
5. New Fridge magnet for Furniture removals (residential)
6. New fridge magnet for Corporate Relocations (business)
1. Residential Logo
a. We require the logo to be translated into a high quality digital image with no modifications.
(see attached resilogo.jpg)
2. Residential Logo
a. We require the logo to be edited (add the word corporate relocations) be translated into a high quality digital image.
(see attached corplogo.jpg)
3. Using the resilogo please make a new business card for our business.
a. Please see the web site https://www.larkbendcarters.com.au for colours and inspiration.
b. The residential business card needs the following information:
i. Business Name (using the residential logo).
ii. Free Call: 1800 LB Cart (the L, B and Cart much be the same colour as the logo).
iii. Website: www.LarkbendCarters.com.au
iv. Address: 4/17 Ormsdale Court, VIC 3264
v. Email: cart@LarkbendCarters.com.au
vi. backof Card:
Review our service
www.PennantOrbit.com.au
Services: Local, Country, Interstate | Furniture Removals | Piano, Billiard Tables & Antiques
4. Using the corplogo please make a new business card for our business.
b. The corporate business card needs the following information:
i. Business Name (using the corporate logo).
v. Email: corporate@LarkbendCarters.com.au
vi. Back of Card:
Review our service
www.PennantOrbit.com.au
Services: Corporate relocations | Office equipment moves | Packing Service | Packing Materials
5. Using the resilogo please make a new fridge magent for our business.
b. The residential fidge magnet needs the following information:
iv. Services: Local, Country, Interstate | Furniture Removals | Piano, Billiard Tables & Antiques
6. Using the corplogo please make a new fridge magent for our business.
b. The corporate fidge magnet needs the following information:
iv. Services: Local, Country, Interstate | Corporate relocations
Target Market(s)
Residential Furniture Removals and Corporate Office relocations
Industry/Entity Type
Business
Contact Information for Business Card
Please see full brief for six items required
Requirements
Must have
- Clean simple, easy to read
Nice to have
- fresh, stand out, eye catching
Should not have
- plain, standard, boring, general

```html
<!DOCTYPE html>
<html lang="en">
<head>
<meta charset="utf-8">
<title>Larkbend Carters — Business Card</title>
<link rel="stylesheet" href="https://fonts.googleapis.com/css2?family=Archivo+Black&family=Michroma&family=Arimo:wght@400&display=swap">
<style>
  :root {
    --stage: #2b2a27;
    --card-black: #050505;
    --card-white: #ffffff;
    --brand-yellow: #f6c417;
    --brand-red: #e6202b;
    --brand-green: #1fae4b;
    --ink: #111111;
  }
  * { box-sizing: border-box; margin: 0; padding: 0; }
  html, body {
    width: 1200px; height: 856px; overflow: hidden;
    background: var(--stage);
  }
  .canvas { position: relative; width: 1200px; height: 856px; }

  .card {
    position: absolute;
    width: 620px; height: 380px;
    border-radius: 30px;
    background: var(--card-black);
    overflow: hidden;
    box-shadow: 0 14px 30px rgba(0,0,0,0.45);
  }
  .card--front { left: 40px; top: 446px; }
  .card--back  { left: 540px; top: 30px; }

  /* Front */
  .front__band {
    height: 150px; background: var(--card-white);
    display: flex; align-items: center; justify-content: center;
  }
  .brand-name {
    font-family: "Archivo Black", sans-serif;
    font-size: 50px; letter-spacing: 1px;
    color: var(--brand-green);
    text-transform: uppercase;
  }
  .front__body { padding: 26px 40px 0; }
  .freecall {
    font-family: "Archivo Black", sans-serif;
    font-size: 38px; color: var(--card-white);
    white-space: nowrap;
  }
  .freecall .lb { color: var(--brand-yellow); }
  .freecall .cart { color: var(--brand-green); }
  .contact {
    margin-top: 18px; list-style: none;
    font-family: "Arimo", sans-serif; font-size: 21px; line-height: 1.35;
  }
  .contact .web { color: var(--brand-yellow); }
  .contact .addr { color: var(--brand-red); }
  .contact .mail { color: var(--brand-green); }

  /* Back */
  .back__band {
    height: 105px; background: var(--card-white);
    display: flex; flex-direction: column; align-items: center; justify-content: center;
    color: var(--ink);
  }
  .review-title {
    font-family: "Michroma", sans-serif; font-size: 20px; letter-spacing: 2px;
  }
  .review-url {
    font-family: "Arimo", sans-serif; font-size: 12px; margin-top: 2px;
  }
  .back__body {
    display: flex; justify-content: space-between;
    padding: 40px 34px 0 40px;
    font-family: "Archivo Black", sans-serif; font-size: 24px; line-height: 1.15;
  }
  .services { list-style: none; }
  .services--area { margin-top: 44px; }
  .services--area li:nth-child(2) { padding-left: 14px; }
  .services--area li:nth-child(3) { padding-left: 30px; }
  .services--type li:nth-child(2) { padding-left: 16px; }
  .services--type li:nth-child(3) { padding-left: 30px; }
  .services--type li:nth-child(4) { padding-left: 46px; }
  .c-yellow { color: var(--brand-yellow); }
  .c-red { color: var(--brand-red); }
  .c-green { color: var(--brand-green); }
</style>
</head>
<body>
<main class="canvas">

  <section class="card card--back" aria-label="Business card back">
    <header class="back__band">
      <p class="review-title">REVIEW OUR SERVICE</p>
      <p class="review-url">www.PennantOrbit.com.au</p>
    </header>
    <div class="back__body">
      <ul class="services services--area">
        <li class="c-yellow">Local</li>
        <li class="c-red">Country</li>
        <li class="c-green">Interstate</li>
      </ul>
      <ul class="services services--type">
        <li class="c-green">Furniture Removals</li>
        <li class="c-yellow">Piano</li>
        <li class="c-red">Billiard Tables</li>
        <li class="c-green">&amp; Antiques</li>
      </ul>
    </div>
  </section>

  <section class="card card--front" aria-label="Business card front">
    <header class="front__band">
      <h1 class="brand-name">Larkbend Carters</h1>
    </header>
    <div class="front__body">
      <p class="freecall">Free Call: 1800 <span class="lb">LB</span> <span class="cart">Cart</span></p>
      <ul class="contact">
        <li class="web">Website: www.LarkbendCarters.com.au</li>
        <li class="addr">Address: 4/17 Ormsdale Court, VIC 3264</li>
        <li class="mail">Email: cart@LarkbendCarters.com.au</li>
      </ul>
    </div>
  </section>

</main>
</body>
</html>
```